Business Card for Multi-Brand Sportswear Company

We are looking for a business card which represents our company and the multiple brands within it.

The company: Fen Athletics (LTD)
The brands: Fen, TavaPuni, ElmStretch, Grit and Rain

Employees using these cards would be representing Fen Athletics, rather than any of the individual brands. You will see a current design within the uploaded files, to give some inspiration. The actual text of the brands is not necessary, but the logos should be on there is some format.

Our creative minds on this are stretched, so we are looking for someone to make this their own, and show us what a good business card should look like.

We may like to get these printed with spot gloss, so keep that in mind with your designs.

www.fenathletics.co.uk

Industry/Entity Type

Business

Contact Information for Business Card

Leo Pemberton-Hale
Operations Manager
(+44) 1632 960 418
Leo@fenathletics.co.uk
www.fenathletics.co.uk

Font styles to use
Sans Serif
Other font styles liked:
• Eurostile

Colors
ffffff

Requirements
Nice to have
• Dark (black) background

```html
<!DOCTYPE html>
<html lang="en">
<head>
<meta charset="utf-8">
<title>Fen Athletics business card</title>
<link rel="stylesheet" href="https://fonts.googleapis.com/css2?family=Saira:wght@400;500;600&display=swap">
<style>
  :root {
    --page: #ececec;
    --card-white: #ffffff;
    --card-dark: #2a2a2a;
    --card-dark-soft: #333333;
    --ink-light: #ffffff;
    --ink-muted: #e2e2e2;
    --ink-dark: #2b2b2b;
    --accent: #e3262b;
    --chip: #6b5468;
    --chip-grey: #9a9a9a;
  }
  * { box-sizing: border-box; margin: 0; padding: 0; }
  html, body { width: 1200px; height: 586px; overflow: hidden; }
  body {
    background: var(--page);
    font-family: "Saira", sans-serif;
    position: relative;
  }
  .card {
    position: absolute;
    top: 129px;
    width: 501px;
    height: 300px;
    background: var(--card-white);
    overflow: hidden;
  }
  .card--front { left: 65px; }
  .card--back { left: 608px; }

  .card__field {
    position: absolute;
    left: 0;
    width: 100%;
    background: radial-gradient(ellipse at 40% 40%, var(--card-dark-soft), var(--card-dark) 75%);
  }
  .card--front .card__field { top: 38px; height: 223px; }
  .card--back .card__field { top: 0; height: 261px; }

  .wordmark {
    position: absolute;
    display: flex;
    align-items: center;
    gap: 10px;
    color: var(--ink-light);
    font-weight: 500;
    white-space: nowrap;
    transform: translateX(-50%);
  }
  .wordmark__mark {
    width: 14px; height: 14px;
    background: var(--accent);
  }
  .card--front .wordmark { left: 251px; top: 126px; font-size: 40px; line-height: 50px; }
  .card--front .wordmark__mark { width: 20px; height: 20px; }
  .card--back .wordmark { left: 250px; top: 26px; font-size: 26px; line-height: 34px; }

  .identity {
    position: absolute;
    right: 281px;
    top: 132px;
    text-align: right;
    color: var(--ink-light);
  }
  .identity__name { font-size: 17px; font-weight: 600; line-height: 24px; }
  .identity__role { font-size: 11.5px; color: var(--ink-muted); line-height: 18px; margin-bottom: 6px; }
  .identity__address { font-style: normal; font-size: 12.5px; font-weight: 500; line-height: 17px; }

  .divider {
    position: absolute;
    left: 256px;
    top: 131px;
    width: 2px;
    height: 96px;
    background: linear-gradient(to bottom, transparent, var(--accent), transparent);
  }

  .contact {
    position: absolute;
    left: 284px;
    top: 144px;
    list-style: none;
    color: var(--ink-light);
    font-size: 11.5px;
  }
  .contact__item { display: flex; align-items: center; gap: 8px; height: 24.5px; }
  .contact__icon { width: 13px; height: 12px; fill: var(--accent); flex: none; }

  .brand-row {
    position: absolute;
    top: 261px;
    left: 0;
    width: 100%;
    height: 39px;
    display: flex;
    justify-content: center;
    align-items: center;
    gap: 14px;
    font-size: 11px;
    font-weight: 600;
    color: var(--ink-dark);
  }
</style>
</head>
<body>
  <section class="card card--front">
    <div class="card__field" role="img" aria-label="Dark charcoal faceted polygon texture"></div>
    <div class="wordmark"><span class="wordmark__mark"></span>Fen Athletics</div>
  </section>

  <section class="card card--back">
    <div class="card__field" role="img" aria-label="Dark charcoal faceted polygon texture"></div>
    <div class="wordmark"><span class="wordmark__mark"></span>Fen Athletics</div>

    <div class="identity">
      <p class="identity__name">Dale Ashworth</p>
      <p class="identity__role">Managing Director</p>
      <address class="identity__address">Ridge Farm, Oakby<br>Fenwick, FN4 2QT</address>
    </div>

    <div class="divider"></div>

    <ul class="contact">
      <li class="contact__item">
        <svg class="contact__icon" viewBox="0 0 14 12"><path d="M1 4c0-2 2-3 6-3s6 1 6 3l-3 1-1-2H5L4 5 1 4zM3 6h8l1 5H2z"/></svg>
        +44 (0)1632 960418
      </li>
      <li class="contact__item">
        <svg class="contact__icon" viewBox="0 0 14 12"><path d="M3 0h8v3H3zM0 4h14v5h-3V7H3v2H0zM4 8h6v4H4z"/></svg>
        (555) 014-2290
      </li>
      <li class="contact__item">
        <svg class="contact__icon" viewBox="0 0 14 12"><path d="M0 1h14v10H0zM1 2l6 5 6-5"/><path d="M1 2l6 5 6-5" fill="none" stroke="#2a2a2a" stroke-width="1.2"/></svg>
        dale@fenathletics.co.uk
      </li>
    </ul>

    <div class="brand-row">
      <span>Fen</span>
      <span>TavaPuni</span>
      <span>ElmStretch</span>
      <span>Grit and Rain</span>
    </div>
  </section>
</body>
</html>
```